SaaS / Consulting / Solution website redesign

We need a website design that:
- Is completely different than our current design : https://plumvessel.net
- Has a very minimal amount of copy
- Changes our positioning from a SaaS application to a solutions company. Solutions company means that we help our customers solve their problems with consulting, training, and tools. An example of a solutions company is here: https://oldpages.example/web/20130111103320/http://www.brindlework.com:80/
- Does not make us look like a start up
- Is more people oriented than technology oriented

We need a designer that:
- Is a rebel at heart
- Is a minimalist
- Tells us why our current site sucks
- Can disagree with us
- Can also do copywriting or already has a copywriter that can help
- Is ok with saying we have capability that we don't in order to see if people actually want that
- Can understand the difference between our grand vision and where we need to focus ourselves today in order to get there

Who we are:
- Entrepreneurs
- Programmers
- Consultants
- Investors

Here's our design goals:
#1 Get customers, investors, employers, and partners excited about our unique and clearly articulated value proposition
#2 Get people to contact us asking for help with their programs
#3 Position ourselves as an expert in the skills based volunteering, mentorship, and group collaboration
#4 Make it easy for people, who already know who we are, to register online

What our grand vision is:
- Create a marketplace where any person can go to our site and find time with anyone they need to meet with. Whether that is their hair stylist, school advisor, parent of your kids class, dentist, attorney, etc.

What will you get if you win:
- In addition to the prize of this project we will have many landing pages and other revisions we will need in the future. We currently don't have a designer or copywriter and need to add that capability to our team

Who do we need to appeal to:
- Directors that are launching innovative programs inside organizations
- IT personnel who are trying to disqualify our technology so they don't have to support it or deal with it when it doesn't go well
- Enterprise IT architects who don't want our product being on its own island within their organization totally incompatible with everything else. Architects which are trying to assess how our platform will co-exist with all their other platforms
- Vice Presidents who want to help their directors understand that we don't have enough experience to help them
- Program managers who have to juggle a million things and need a tool that actually helps instead of confuses them and adds more work for them.
- Program managers & directors that have been given ambiguous goals by their board of directors like "improve retention, increase engagement, create innovation, get people to collaborate." And who have no idea where to start or how to deliver on things like that.
- Program managers, directors, and vice presidents that are trying to understand how our technology and services fit into their existing technology and capability
- Employees who are bored and uninspired with their current tools and are hoping for some excitement in their life. Kind of like candy or a double espresso.
- Investors who think, our company like all the rest, are going to waste their money and make them look like a fool

Other information:
-The CSS and html needs to be responsive

-Our registration onboarding flow needs to collect this information:
User first name
user last name
user email
(verify their email)
user phone number
(verify their phone number)
User profile image (optional)
User profile summary (optional, like a bio, freeform text fiels)
If applicable: Register their organization
Organization name
Organization image (optional)
Account Mailing address
account Billing address (could be same as mailing address)
account Billing email address (could be same as user address)
account Product selection (pricing tier)
account Credit card information

The designs I am getting are a good start but they are only the front page. I just want you to know that I am expecting and need more than a landing page to complete the design. I will likely need a page that outlines the benefits and features of the product itself, how its different than our competitors, which will not be on the front page. I will need a registration flow. I will need a blog page design so we can post blog articles, I will need a team page, a page that goes into detail on our training, our services. I will likely need a page that shows all news and media we have been in. I need to show customer and user quotes, case studies, a way to contact us, partners, general resources like on collaboration, product tutorials, customers. I need the site to address a comprehensive set of needs. I need that design to be consistent and thorough. I know what PlateHarbor is. I'm not using because I need more than a template that was customized. I need to be unique and match our brand thoughtfully, beautifully, and artistically. Someone asked me a question about how Murmly is similar to our tool in the way it is referred by end users and purchased by managers. Our website needs to primarily talk to the managers as I explained in the brief but it needs to appear cool and exciting to our end-users without focusing on the technology too much. Murmly is a tool that teams use to collaborate in small and large enterprises. The value prop for them is that communication is easier. But they don't put that on their website. Why? Because the users of the technology won't go to the website to find out information on it, they get their information from someone who is using it and demos it to them. When Ines tells her manager Otto "Lets get murmly, Ruth is using it at her company and its great" Ines's manager doesn't know anything about murmly so she promptly googles it. The most important thing from Ines's perspective is that Otto agrees to try it out. Otto's biggest concern is that productivity will be enhanced to degraded. Murmly knows this and so on the front page they know they are talking to Otto NOT Ines because Ines is already sold on it and doesn't need to get sold on the website. Ines is end user. Otto is the purchaser. We have the same problem and so our end users are not the ones purchasing our product, their managers are purchasing our product. We get referred by our end users and vetted by their managers. Hope this helps! Thank you for looking at this project!  Added Wednesday, June 7, 2017

Another observation I am having about the designs being submitted. I believe we used the animations on our current website because animations / cartoons connect with the "inner child" in our users. Whatever that means :-). I think it's what makes our brand fun. I have a hard time imagining that we could make the design fun looking without animations but I'm sure it can be achieved. I also recognize that blending pictures of real people and animations is hard. So either we must masterfully blend them, use only animations, or make the real people have a LOT of fun! So far most of the designs while achieve the goal of appealing to the serious Vice Presidents and directors, they are not doing a good job at appealing to the overworked program managers and bored employees. There seems to stand another challenge with animations which is animations are hard to find and/or create that achieve the message / emotion we are trying to communicate. I don't have any good answers for this but I will say we can hire both animators and illustrators if we need to. All you have to do is communicate the effect in the website design with some simpler version maybe not the end illustration or animation itself. Added Wednesday, June 7, 2017

• Sex appeal and a sense of humor. Copy that makes people excited and clairvoyant about our potential.
• Boring renditions of other non-inspiring websites

```html
<!DOCTYPE html>
<html lang="en">
<head>
<meta charset="utf-8">
<title>Plumvessel — Blog</title>
<link href="https://fonts.googleapis.com/css2?family=Roboto:wght@300;400;500&display=swap" rel="stylesheet">
<style>
:root{
  --brand-blue:#0aa6f0;
  --hero-blue:#3db3e6;
  --date-blue:#2aa9e0;
  --login-green:#7dc67d;
  --brand-green:#6cc16c;
  --ink:#1c1c1c;
  --body:#777777;
  --nav:#8a8a8a;
  --rule:#d9d9d9;
  --footer-bg:#f0f1f4;
  --white:#ffffff;
}
*{box-sizing:border-box;margin:0;padding:0}
html,body{width:1071px;height:1200px;overflow:hidden;background:var(--white)}
body{position:relative;font-family:'Roboto',sans-serif;color:var(--ink)}
a{text-decoration:none;color:inherit}

.site-header{position:absolute;left:0;top:0;width:1071px;height:86px}
.brand{position:absolute;display:flex;align-items:center;gap:7px}
.brand-mark{width:28px;height:28px;border:3px solid var(--brand-green);border-radius:50%}
.brand-name{font-size:18px;font-weight:400;color:var(--brand-green)}
.site-header .brand{left:146px;top:34px}
.main-nav{position:absolute;top:49px;left:0;font-size:8.5px;font-weight:500;color:var(--nav)}
.main-nav a{position:absolute;white-space:nowrap;letter-spacing:.3px}
.main-nav a.is-active{color:var(--brand-blue)}
.btn-login,.btn-register{position:absolute;top:38px;height:27px;display:flex;align-items:center;justify-content:center;color:var(--white);font-size:9.5px;font-weight:500;letter-spacing:.3px}
.btn-login{left:777px;width:60px;background:var(--login-green)}
.btn-register{left:844px;width:86px;background:var(--brand-blue)}

.hero{position:absolute;left:0;top:86px;width:1071px;height:145px;background:var(--hero-blue)}
.hero-title{position:absolute;left:180px;top:52px;display:flex;align-items:center;gap:16px;color:var(--white)}
.hero-title .mark{width:40px;height:40px;border:4px solid var(--white);border-radius:50%}
.hero-title h1{font-size:42px;font-weight:300;letter-spacing:1px}
.btn-subscribe-hero{position:absolute;left:754px;top:58px;width:172px;height:38px;border:2px solid var(--white);color:var(--white);font-size:24px;font-weight:300;display:flex;align-items:center;justify-content:center;letter-spacing:.5px}

.breadcrumb{position:absolute;left:143px;top:249px;font-size:9.5px;color:var(--ink)}
.breadcrumb span{color:var(--date-blue)}
.site-search{position:absolute;left:750px;top:240px;width:155px;height:27px;border:1px solid #cfcfcf;font-size:11px;color:#444;padding:6px 7px}
.search-icon{position:absolute;left:909px;top:247px}
.divider{position:absolute;left:143px;top:275px;width:783px;height:1px;background:var(--rule)}

.post{position:absolute;width:249px}
.post-thumb{width:249px;height:127px;border:1px solid #e2e2e2}
.post-body{padding:0 10px}
.post-date{font-size:9.5px;color:var(--date-blue);margin-top:10px}
.post-title{font-size:11.5px;font-weight:400;line-height:16px;margin-top:6px;color:var(--ink)}
.post-excerpt{font-size:9.4px;line-height:11.3px;color:var(--body);margin-top:5px;font-weight:400;height:45px}
.btn-read{display:inline-block;margin-top:8px;width:61px;height:14px;line-height:14px;text-align:center;background:var(--brand-blue);color:var(--white);font-size:7.6px;font-weight:500}

.thumb-network{background:linear-gradient(135deg,#f7f8fa,#dbe9f7)}
.thumb-laptop{background:linear-gradient(135deg,#4fb3c0,#5bbcc8)}
.thumb-desk{background:linear-gradient(135deg,#7a4a2c,#b07a4f)}
.thumb-growth{background:linear-gradient(135deg,#f2f4f6,#c9d2da)}
.thumb-devices{background:linear-gradient(135deg,#ffffff,#d3e5f4)}
.thumb-idea{background:linear-gradient(135deg,#f1f1f1,#ecdcae)}

.pagination{position:absolute;top:878px;left:0;font-size:11px;color:var(--ink)}
.pagination a{position:absolute;top:5px;white-space:nowrap}
.pagination .is-current{top:0;left:457px;width:22px;height:22px;border:2px solid var(--brand-blue);display:flex;align-items:center;justify-content:center}

.site-footer{position:absolute;left:0;top:934px;width:1071px;height:266px;background:var(--footer-bg)}
.site-footer .brand{left:143px;top:40px}
.site-footer .brand-mark{width:32px;height:32px}
.site-footer .brand-name{font-size:19px}
.footer-about{position:absolute;left:143px;top:100px;width:395px;font-size:9.6px;line-height:16px;color:#333;font-weight:400}
.footer-links{position:absolute;top:104px;font-size:8px;color:#555;letter-spacing:.3px;left:0}
.footer-links a{position:absolute;white-space:nowrap}
.btn-demo,.btn-brochure,.btn-newsletter{position:absolute;height:24px;display:flex;align-items:center;justify-content:center;font-size:8.6px;font-weight:500;letter-spacing:.4px}
.btn-demo{left:152px;top:158px;width:90px;background:var(--brand-blue);color:var(--white)}
.btn-brochure{left:250px;top:158px;width:122px;background:var(--white);color:var(--brand-blue)}
.newsletter-field{position:absolute;left:679px;top:160px;width:170px;height:24px;border-bottom:1px solid #d6d6d6;font-size:7.5px;color:#c9c9c9;padding-top:8px}
.btn-newsletter{left:856px;top:160px;width:71px;background:var(--white);color:var(--brand-blue)}
.footer-rule{position:absolute;left:143px;top:216px;width:783px;height:1px;background:#d8d9dc}
.footer-legal{position:absolute;top:236px;font-size:9px;color:#444;white-space:nowrap}
.social{position:absolute;top:231px;width:9px;height:9px;border-radius:50%;background:#888}
</style>
</head>
<body>

<header class="site-header">
  <a class="brand" href="#"><span class="brand-mark"></span><span class="brand-name">Plumvessel</span></a>
  <nav class="main-nav">
    <a class="is-active" style="left:425px">Home</a>
    <a style="left:481px">Product</a>
    <a style="left:547px">About</a>
    <a style="left:605px">Library</a>
    <a style="left:667px">Careers</a>
    <a style="left:733px">Contact</a>
  </nav>
  <a class="btn-login" href="#">Login</a>
  <a class="btn-register" href="#">Register Now</a>
</header>

<section class="hero">
  <div class="hero-title"><span class="mark"></span><h1>BLOG</h1></div>
  <a class="btn-subscribe-hero" href="#">SUBSCRIBE</a>
</section>

<div class="breadcrumb">Home &gt; <span>Blog</span></div>
<div class="site-search">Search Site</div>
<svg class="search-icon" width="14" height="14" viewBox="0 0 14 14"><circle cx="5.5" cy="5.5" r="4" fill="none" stroke="#6cc16c" stroke-width="1.6"/><line x1="8.5" y1="8.5" x2="13" y2="12" stroke="#6cc16c" stroke-width="2"/></svg>
<div class="divider"></div>

<article class="post" style="left:143px;top:296px">
  <div class="post-thumb thumb-network" role="img" aria-label="Line illustration of connected devices and documents"></div>
  <div class="post-body">
    <p class="post-date">June 16, 2017</p>
    <h2 class="post-title">Your board said "boost engagement." Here is where to actually start.</h2>
    <p class="post-excerpt">Vague goals land on program managers every day. We break them into three small, human steps your people will actually want to take this quarter.</p>
    <a class="btn-read" href="#">Read More</a>
  </div>
</article>
<article class="post" style="left:410px;top:296px">
  <div class="post-thumb thumb-laptop" role="img" aria-label="Illustration of a laptop linked to two apps"></div>
  <div class="post-body">
    <p class="post-date">June 15, 2017</p>
    <h2 class="post-title">No new islands: how our tools fit the systems your IT team runs.</h2>
    <p class="post-excerpt">Architects ask how we live beside everything else. Short answer: single sign-on, open calendars and clean exports, so nothing ends up stranded.</p>
    <a class="btn-read" href="#">Read More</a>
  </div>
</article>
<article class="post" style="left:678px;top:296px">
  <div class="post-thumb thumb-desk" role="img" aria-label="Photo of a wooden desk with laptop, coffee and charts"></div>
  <div class="post-body">
    <p class="post-date">June 14, 2017</p>
    <h2 class="post-title">Mentorship that sticks: lessons from a year of pairing people.</h2>
    <p class="post-excerpt">Matching is the easy part. Keeping mentors and mentees meeting is where programs fail. Here is the training and rhythm that kept ours going.</p>
    <a class="btn-read" href="#">Read More</a>
  </div>
</article>

<article class="post" style="left:143px;top:579px">
  <div class="post-thumb thumb-growth" role="img" aria-label="Illustration of a businessman watering a tree"></div>
  <div class="post-body">
    <p class="post-date">June 13, 2017</p>
    <h2 class="post-title">Skills-based volunteering grows people, not just good feelings.</h2>
    <p class="post-excerpt">When employees lend real skills to real causes, retention climbs. A simple consulting playbook for launching a volunteer program in six weeks.</p>
    <a class="btn-read" href="#">Read More</a>
  </div>
</article>
<article class="post" style="left:410px;top:579px">
  <div class="post-thumb thumb-devices" role="img" aria-label="Illustration of desktop, laptop, tablet and phones"></div>
  <div class="post-body">
    <p class="post-date">June 12, 2017</p>
    <h2 class="post-title">Fewer tabs, more talking: a manager's guide to team collaboration.</h2>
    <p class="post-excerpt">Your people are bored of tools that add work. Here is how to find time with the right colleague in seconds and get back to doing things together.</p>
    <a class="btn-read" href="#">Read More</a>
  </div>
</article>
<article class="post" style="left:678px;top:579px">
  <div class="post-thumb thumb-idea" role="img" aria-label="Illustration of a light bulb, rocket and envelope"></div>
  <div class="post-body">
    <p class="post-date">June 11, 2017</p>
    <h2 class="post-title">From idea to launch: get your program running in one afternoon.</h2>
    <p class="post-excerpt">Register, invite your team and pick a plan. Our onboarding takes minutes, and our consultants stay with you until the first match goes live.</p>
    <a class="btn-read" href="#">Read More</a>
  </div>
</article>

<nav class="pagination">
  <a class="is-current">1</a>
  <a style="left:490px">2</a>
  <a style="left:514px">3</a>
  <a style="left:539px">4</a>
  <a style="left:564px">....</a>
  <a style="left:594px">10</a>
</nav>

<footer class="site-footer">
  <a class="brand" href="#"><span class="brand-mark"></span><span class="brand-name">Plumvessel</span></a>
  <p class="footer-about">We help organizations bring people together through consulting, training and tools for mentorship, volunteering and collaboration.</p>
  <nav class="footer-links">
    <a style="left:684px">CONTACT</a>
    <a style="left:782px">ABOUT</a>
    <a style="left:864px">IMPRESSUM</a>
  </nav>
  <a class="btn-demo" href="#">REQUEST DEMO</a>
  <a class="btn-brochure" href="#">DOWNLOAD BROCHURE</a>
  <div class="newsletter-field">YOUR@EMAIL.COM</div>
  <a class="btn-newsletter" href="#">SUBSCRIBE</a>
  <div class="footer-rule"></div>
  <p class="footer-legal" style="left:145px">© 2017 Plumvessel Inc All rights reserved | Plumvessel® is a registered trademark of Plumvessel Inc</p>
  <a class="footer-legal" style="left:578px">Blog</a>
  <a class="footer-legal" style="left:626px">Press</a>
  <span class="social" style="left:843px" aria-label="Social link 1"></span>
  <span class="social" style="left:880px" aria-label="Social link 2"></span>
  <span class="social" style="left:917px" aria-label="Social link 3"></span>
</footer>

</body>
</html>
```